Business Card Design Project

I am opening a skin care studio called Glow Haven by Marisol. I will be offering a wide range of unique and affordable skin services including facials, chemical peels, microdermabrasion treatments, body wraps, salt glows, all waxing and eye lash extensions. If the business cards depicts what I would like, this would lead to brochures, web design, signs, etc.

Project Deadline Extended
Reason: A request to extend deadline was requested. I will be more than happy to accommodate.

Industry/Entity Type

Business

Requirements
Nice to have
• facial features so prospective client clearly identifies what type of business this is. Not stuffy or boring "spa" looking graphics. I am focusing just on face, body, waxing, eyelashes. No massage or nails.

```html
<!DOCTYPE html>
<html lang="en">
<head>
<meta charset="utf-8">
<title>Glow Haven by Marisol — Business Card</title>
<link rel="stylesheet" href="https://fonts.googleapis.com/css2?family=Questrial&display=swap">
<style>
  :root {
    --page-bg: #f2f2f2;
    --card-black: #141414;
    --card-black-edge: #222222;
    --card-paper: #f7f6f3;
    --ink: #111111;
    --ink-light: #ffffff;
    --wash-blue: #4f7fc0;
    --wash-sky: #9fc8e6;
    --wash-pink: #e77fae;
    --wash-lilac: #b7a6d8;
    --wash-cream: #f4ece6;
  }

  * { margin: 0; padding: 0; box-sizing: border-box; }

  html, body {
    width: 1200px;
    height: 1200px;
    overflow: hidden;
    background: var(--page-bg);
    font-family: "Questrial", "Century Gothic", sans-serif;
  }

  .sheet {
    width: 1200px;
    height: 1200px;
    display: flex;
    flex-direction: column;
    align-items: center;
    justify-content: center;
    gap: 64px;
  }

  .card {
    position: relative;
    width: 880px;
    height: 503px;
    overflow: hidden;
    box-shadow: 0 6px 24px rgba(0, 0, 0, 0.12);
  }

  /* Front */
  .card--front {
    background: linear-gradient(160deg, var(--card-black-edge) 0%, var(--card-black) 60%);
    color: var(--ink-light);
    display: flex;
    flex-direction: column;
    align-items: center;
    justify-content: center;
  }

  .brand-name {
    font-size: 58px;
    font-weight: 400;
    letter-spacing: 0.04em;
    line-height: 1;
  }

  .brand-owner {
    margin-top: 12px;
    font-size: 25px;
    letter-spacing: 0.03em;
  }

  /* Back */
  .card--back {
    background: var(--card-paper);
    color: var(--ink);
  }

  .card-art {
    position: absolute;
    left: 0;
    top: 0;
    width: 520px;
    height: 100%;
    background:
      radial-gradient(ellipse 180px 140px at 140px 150px, var(--wash-blue) 0%, transparent 70%),
      radial-gradient(ellipse 150px 170px at 60px 320px, var(--wash-pink) 0%, transparent 70%),
      radial-gradient(ellipse 200px 200px at 300px 280px, var(--wash-sky) 0%, transparent 75%),
      radial-gradient(ellipse 160px 150px at 230px 420px, var(--wash-lilac) 0%, transparent 75%),
      linear-gradient(90deg, var(--wash-cream), var(--wash-cream));
    -webkit-mask-image: linear-gradient(90deg, #000 55%, transparent 100%);
    mask-image: linear-gradient(90deg, #000 55%, transparent 100%);
  }

  .appointment {
    position: absolute;
    left: 372px;
    top: 98px;
    font-size: 36px;
    line-height: 1.6;
    text-transform: uppercase;
  }

  .appointment-title { display: block; }

  .appointment-line { display: block; }

  .contact {
    position: absolute;
    right: 30px;
    bottom: 44px;
    text-align: right;
    font-size: 26px;
    line-height: 1.28;
  }
</style>
</head>
<body>
  <main class="sheet">
    <section class="card card--front" aria-label="Business card front">
      <h1 class="brand-name">GLOW HAVEN</h1>
      <p class="brand-owner">by marisol</p>
    </section>

    <section class="card card--back" aria-label="Appointment card back">
      <div class="card-art" role="img" aria-label="Watercolour portrait illustration in blue, pink and lilac washes"></div>

      <div class="appointment">
        <span class="appointment-title">Appointment</span>
        <span class="appointment-line">Date ....\....\.....</span>
        <span class="appointment-line">Time .....:.....</span>
      </div>

      <address class="contact" style="font-style: normal;">
        <span>218 Cedar Avenue Millbrook, CO 80999</span><br>
        <span>555-014-2273</span><br>
        <span>glowhavenbymarisol.com</span>
      </address>
    </section>
  </main>
</body>
</html>
```